Body corporate management needs business principle flyer design

We need a one page A4 flyer design for our business principles.
We manage body corporates and strata properties.
VerandaKeep is a new initiative for our company. Its a label that we have given to our principles of business that drive our people, systems and processes to give assurance to our clients that every detail matters.
We would like to be able to include this design in future brochure so we are after 1 x portrait and 1 x landscape.
The design needs to portray professionalism.
We would like to see designs that use the colour red. (see attached logo).

Target Market(s)

Professionals

Industry/Entity Type

Business

Font styles to use
Sans Serif

Requirements
Must have
• VerandaKeep logo, provide the design file and as pdf
Nice to have
• the use of the colour red from the logo

```html
<!DOCTYPE html>
<html lang="en">
<head>
<meta charset="utf-8">
<title>VerandaKeep Principles of Business</title>
<link href="https://fonts.googleapis.com/css2?family=Open+Sans:wght@400;600;700&family=Arimo:wght@400;700&display=swap" rel="stylesheet">
<style>
:root{
  --red:#e63c2e;
  --band-grey:#e4e4e6;
  --ink:#1f1f1f;
  --body:#333333;
  --paper:#ffffff;
  --backdrop:#d9d9d9;
}
*{box-sizing:border-box;margin:0;padding:0}
html,body{width:1012px;height:1200px;overflow:hidden;background:var(--backdrop)}
.flyer{position:absolute;left:82px;top:0;width:848px;height:1200px;background:var(--paper);box-shadow:0 0 12px rgba(0,0,0,.25);font-family:"Open Sans",Arial,sans-serif;color:var(--body)}
.header-band{position:absolute;left:0;top:61px;width:848px;height:83px}
.header-band svg{position:absolute;left:0;top:0}
.header-title{position:absolute;left:110px;top:14px;color:#fff;font-family:"Arimo",Arial,sans-serif}
.header-title .name{font-size:30px;font-weight:700;line-height:32px;letter-spacing:-.3px}
.header-title .sub{font-size:16px;font-weight:700;line-height:20px}
.brand-name{position:absolute;left:500px;top:15px;font-size:44px;font-weight:400;color:var(--red);line-height:56px;letter-spacing:-.5px}
.headline{position:absolute;left:110px;top:190px;width:640px;font-family:"Arimo",Arial,sans-serif;font-weight:700;font-size:19px;line-height:25px;color:var(--ink)}
.principle{position:absolute}
.principle.left{left:110px;width:355px}
.principle.right{left:466px;width:295px}
.principle h2{display:flex;align-items:center;gap:12px;font-size:18.5px;font-weight:700;color:var(--red);height:38px;line-height:38px}
.principle h2 svg{flex:0 0 auto}
.principle p{margin-top:6px;font-size:13px;line-height:15.6px}
.contact-band{position:absolute;left:356px;top:1120px;width:492px;height:80px}
.contact-band svg{position:absolute;left:0;top:0}
.contact-text{position:absolute;left:10px;right:0;top:10px;text-align:center;color:#fff;font-family:"Arimo",Arial,sans-serif;font-size:15px;line-height:19px}
.contact-text strong{font-weight:700}
</style>
</head>
<body>
<main class="flyer">
  <header class="header-band">
    <svg width="848" height="83" viewBox="0 0 848 83">
      <polygon points="333,0 848,0 848,83 319,83" fill="var(--band-grey)"/>
      <polygon points="0,0 329,0 315,83 0,83" fill="var(--red)"/>
    </svg>
    <div class="header-title">
      <div class="name">VerandaKeep</div>
      <div class="sub">Principles of Business</div>
    </div>
    <div class="brand-name">VerandaKeep</div>
  </header>

  <h1 class="headline">VerandaKeep Is Our Principles Of Business That Drive Our People, Systems And Processes To Give Assurance To Our Clients That Every Detail Matters.</h1>

  <section class="principle left" style="top:298px">
    <h2><svg width="44" height="30" viewBox="0 0 44 30"><rect x="2" y="9" width="10" height="12" fill="var(--red)"/><polygon points="12,9 34,1 34,29 12,21" fill="var(--red)"/><rect x="5" y="21" width="5" height="8" fill="var(--red)"/><line x1="37" y1="15" x2="43" y2="15" stroke="var(--red)" stroke-width="2"/><line x1="37" y1="8" x2="42" y2="5" stroke="var(--red)" stroke-width="2"/><line x1="37" y1="22" x2="42" y2="25" stroke="var(--red)" stroke-width="2"/></svg>Client Experience</h2>
    <p>Our promise is to pursue excellence and to continually deliver a solutions based service. We achieve this through active engagement, open channels of communication and a serviced led team with the dedicated resources to listen, engage and implement.</p>
  </section>

  <section class="principle left" style="top:508px">
    <h2><svg width="44" height="30" viewBox="0 0 44 30"><polygon points="2,8 14,2 26,10 18,18" fill="#9a9a9a"/><polygon points="42,8 30,2 16,12 26,26 34,20" fill="var(--red)"/><rect x="4" y="14" width="8" height="4" fill="#9a9a9a" transform="rotate(35 8 16)"/></svg>Loyalty</h2>
    <p>We seek to develop a life-time relationship with our clients, building trust by acting with integrity, honesty and courtesy. We achieve this due to our expert approach to strata management and providing a responsive service to our clients.</p>
  </section>

  <section class="principle left" style="top:638px">
    <h2><svg width="40" height="34" viewBox="0 0 40 34"><polygon points="30,2 38,10 16,30 8,22" fill="var(--red)"/><polygon points="8,22 16,30 4,33" fill="var(--red)"/><line x1="4" y1="33" x2="22" y2="33" stroke="var(--red)" stroke-width="1.5"/></svg>Education and Guidance</h2>
    <p>We endeavor to always be proactive in client education and guidance. This is achieved by our internal and external communications, comprehensive training programs and cross-departmental collaboration of knowledge sharing.</p>
  </section>

  <section class="principle left" style="top:793px">
    <h2><svg width="40" height="34" viewBox="0 0 40 34"><polygon points="20,1 39,10 1,10" fill="var(--red)"/><rect x="5" y="13" width="5" height="15" fill="var(--red)"/><rect x="17.5" y="13" width="5" height="15" fill="var(--red)"/><rect x="30" y="13" width="5" height="15" fill="var(--red)"/><rect x="1" y="30" width="38" height="4" fill="var(--red)"/></svg>Compliance &amp; Governance</h2>
    <p>We engage and own a position of ‘every detail matters’. We give due diligence to the relevant state and national legislations with which we, our clients and our stakeholders must comply. We regulate and achieve this through a robust system of internal processes and protocols which structure and confirm our deliverables are in line with regulations.</p>
  </section>

  <section class="principle left" style="top:994px">
    <h2><svg width="44" height="34" viewBox="0 0 44 34"><circle cx="15" cy="15" r="10" fill="none" stroke="var(--red)" stroke-width="6" stroke-dasharray="4 3"/><circle cx="15" cy="15" r="8" fill="var(--red)"/><circle cx="15" cy="15" r="3" fill="#fff"/><circle cx="34" cy="25" r="6" fill="none" stroke="var(--red)" stroke-width="4" stroke-dasharray="3 2"/><circle cx="34" cy="25" r="4.5" fill="var(--red)"/><circle cx="34" cy="25" r="1.8" fill="#fff"/></svg>Systems and processes</h2>
    <p>We strive to be the best in our field, by implementing efficiencies without compromising service quality, accuracy or compliance. We continually seek to achieve this by reviewing, updating and adopting continuous improvement strategies, systems and quality processes that deliver outcomes.</p>
  </section>

  <section class="principle right" style="top:296px">
    <h2><svg width="36" height="34" viewBox="0 0 36 34"><circle cx="16" cy="18" r="13" fill="none" stroke="var(--red)" stroke-width="3"/><polyline points="9,17 15,23 33,4" fill="none" stroke="var(--red)" stroke-width="4"/></svg>Quality &amp; Commitment</h2>
    <p>We invest in the recruitment and retention of a quality and diverse team of experienced professionals with a strong focus on continual professional development.  As committed and skilled individuals, we actively promote the cross-departmental collaboration with one another to deliver a well rounded offering.</p>
  </section>

  <section class="principle right" style="top:525px">
    <h2><svg width="40" height="38" viewBox="0 0 40 38"><polyline points="2,3 8,3 14,30 38,30" fill="none" stroke="var(--red)" stroke-width="3"/><rect x="17" y="8" width="12" height="10" fill="var(--red)"/><rect x="19" y="19" width="16" height="9" fill="var(--red)"/><circle cx="16" cy="34" r="3" fill="var(--red)"/><circle cx="34" cy="34" r="3" fill="var(--red)"/></svg>Delivery</h2>
    <p>We empower our teams to deliver an outstanding client service and to be accountable for their actions. We will make sure every detail matters, provide valuable insight and supply information in a clear and timely manner.</p>
  </section>

  <section class="principle right" style="top:668px">
    <h2><svg width="40" height="34" viewBox="0 0 40 34"><polygon points="8,2 32,2 39,11 20,33 1,11" fill="var(--red)"/><polyline points="1,11 39,11" stroke="#fff" stroke-width="1.5" fill="none"/><polyline points="14,2 11,11 20,33 29,11 26,2" stroke="#fff" stroke-width="1.5" fill="none"/></svg>Integrity</h2>
    <p>Our approach to strata management is bound by honesty and a strong set of moral principles. We act in our clients’ best interests with diligence and transparency for understanding and accountability.</p>
  </section>

  <section class="principle right" style="top:810px">
    <h2><svg width="38" height="38" viewBox="0 0 38 38"><polyline points="2,2 2,36 36,36" fill="none" stroke="var(--red)" stroke-width="3"/><rect x="7" y="24" width="5" height="10" fill="var(--red)"/><rect x="15" y="19" width="5" height="15" fill="var(--red)"/><rect x="23" y="22" width="5" height="12" fill="var(--red)"/><rect x="31" y="14" width="4" height="20" fill="var(--red)"/><polyline points="6,20 15,12 23,16 34,4" fill="none" stroke="var(--red)" stroke-width="2.5"/><polygon points="28,4 36,2 34,10" fill="var(--red)"/></svg>Continuous Improvement</h2>
    <p>Our goal is to continually evolve to better our offering and to be adaptable and responsive to change. Our infrastructure supports us to continually mould into the business that is right for our clients.</p>
  </section>

  <section class="principle right" style="top:948px">
    <h2><svg width="34" height="34" viewBox="0 0 34 34"><rect x="2" y="4" width="24" height="28" fill="none" stroke="var(--red)" stroke-width="3"/><line x1="7" y1="12" x2="20" y2="12" stroke="var(--red)" stroke-width="2"/><line x1="7" y1="18" x2="20" y2="18" stroke="var(--red)" stroke-width="2"/><line x1="7" y1="24" x2="15" y2="24" stroke="var(--red)" stroke-width="2"/><polygon points="28,2 33,7 19,22 14,22 14,17" fill="var(--red)"/></svg>Ethical Stance</h2>
    <p>We aim to create a community of ethical business relationships where we contribute our values and services to give our clients outstanding reassurance of our abilities.</p>
  </section>

  <footer class="contact-band">
    <svg width="492" height="80" viewBox="0 0 492 80"><polygon points="14,0 492,0 492,80 0,80" fill="var(--red)"/></svg>
    <div class="contact-text">
      <strong>Contact us</strong><br>
      Tel 0400 112 358&nbsp;&nbsp;Fax: 0400 112 359<br>
      Website: www.verandakeep.com&nbsp;&nbsp;Email:info@verandakeep.co
    </div>
  </footer>
</main>
</body>
</html>
```